New Bicycle shop business card

Hi!
I'm looking for a business card for my new proffesional bike mechanics shop. This shop is only for fixing broken bikes and not selling bikes.
Peferbly a modern and sleek and modern design.
Colors: black, grey, red, white
Information:
Name: Rijwielwerkplaats Vanhoutte
Shop owner: Bart Vanhoutte & Marieke Segers
Website: www.rijwielwerkplaats-vanhoutte.be
Email: info@rijwielwerkplaats-vanhoutte.be
Phone number: +32471902368
Street adres: Kerkweg 46
9940 Bellebeke
Slogan/shop information: Herstellingen van alle merken.
Logo: see files.
Target Market(s)
People who seek a mechanic to fix or upgrade their bikes.
Contact Information for Business Card
Information:
Website: info@rijwielwerkplaats-vanhoutte.be
9940 Bellebeke
Logo: see files.

```html
<!DOCTYPE html>
<html lang="nl">
<head>
<meta charset="utf-8">
<title>Rijwielwerkplaats Vanhoutte – visitekaartje</title>
<link rel="stylesheet" href="https://fonts.googleapis.com/css2?family=Open+Sans:wght@400;600;700;800&display=swap">
<style>
  :root {
    --ink: #060607;
    --paper: #ffffff;
    --red: #ec1c2b;
    --grey: #8a8a8c;
    --stage: #4a4b4e;
    --stage-edge: #2a2b2d;
  }
  * { margin: 0; padding: 0; box-sizing: border-box; }
  html, body { width: 1200px; height: 900px; overflow: hidden; }
  body {
    background: radial-gradient(ellipse at 60% 40%, var(--stage), var(--stage-edge));
    font-family: "Open Sans", Arial, sans-serif;
    position: relative;
  }
  .card {
    position: absolute;
    width: 600px;
    height: 343px;
    border-radius: 26px;
    overflow: hidden;
    box-shadow: 0 18px 40px rgba(0,0,0,.45);
  }
  /* back side */
  .card--back { left: 300px; top: 60px; background: var(--ink); }
  .back-pattern { position: absolute; inset: 0; background: linear-gradient(135deg, #0d0d0e, #050506); }
  .brand {
    position: absolute;
    display: flex; align-items: center; gap: 12px;
    font-weight: 800;
    text-transform: uppercase;
    letter-spacing: .5px;
    line-height: 1.1;
  }
  .brand__mark { width: 22px; height: 22px; border-radius: 50%; background: var(--red); flex: none; }
  .card--back .brand { left: 330px; top: 110px; color: var(--paper); font-size: 19px; }
  .slogan {
    position: absolute; left: 0; right: 0; bottom: 52px;
    text-align: center; color: var(--paper); font-size: 14px; font-weight: 600;
  }
  /* front side */
  .card--front { left: 300px; top: 497px; background: var(--paper); }
  .front-shapes { position: absolute; inset: 0; }
  .card--front .brand { right: 34px; top: 40px; color: var(--ink); font-size: 19px; text-align: right; }
  .card--front .brand__mark { border-radius: 3px; }
  .owners { position: absolute; left: 34px; top: 110px; }
  .owners__label { color: var(--red); font-weight: 600; font-size: 17px; }
  .owners__names { color: var(--grey); font-weight: 700; font-size: 18px; margin-top: -2px; }
  .contact { position: absolute; left: 110px; top: 220px; color: var(--paper); }
  .contact__company { font-weight: 700; font-size: 17px; }
  .contact__role { font-size: 12.5px; margin: 0 0 12px 8px; }
  .contact__list { list-style: none; font-size: 12.5px; line-height: 1.45; margin-left: 16px; }
  .contact__list li { display: flex; align-items: center; gap: 8px; }
  .contact__list svg { width: 12px; height: 12px; fill: none; stroke: var(--paper); stroke-width: 2; }
  .address {
    position: absolute; right: 34px; top: 220px;
    color: var(--paper); font-size: 14px; line-height: 1.3; text-align: right;
  }
</style>
</head>
<body>

  <section class="card card--back" aria-label="Achterkant visitekaartje">
    <div class="back-pattern" role="img" aria-label="Subtiel herhaald merkpatroon in donkergrijs"></div>
    <div class="brand"><span class="brand__mark"></span><span>Rijwielwerkplaats<br>Vanhoutte</span></div>
    <p class="slogan">Herstellingen van alle merken.</p>
  </section>

  <section class="card card--front" aria-label="Voorkant visitekaartje">
    <svg class="front-shapes" viewBox="0 0 600 343" preserveAspectRatio="none" aria-hidden="true">
      <path d="M0,270 C140,205 260,190 360,172 S540,120 600,70 L600,343 L0,343 Z" fill="var(--ink)"/>
      <path d="M110,240 C200,190 300,172 390,155 S540,110 600,52 L600,60 C545,118 460,150 380,166 S220,195 110,240 Z" fill="var(--red)"/>
    </svg>

    <div class="brand"><span class="brand__mark"></span><span>Rijwielwerkplaats<br>Vanhoutte</span></div>

    <div class="owners">
      <p class="owners__label">Shop owner:</p>
      <p class="owners__names">Bart Vanhoutte &amp; Marieke Segers</p>
    </div>

    <div class="contact">
      <p class="contact__company">Rijwielwerkplaats Vanhoutte</p>
      <p class="contact__role">General Manager</p>
      <ul class="contact__list">
        <li><svg viewBox="0 0 24 24"><path d="M5 3h4l2 5-3 2a11 11 0 0 0 6 6l2-3 5 2v4a2 2 0 0 1-2 2A18 18 0 0 1 3 5a2 2 0 0 1 2-2z"/></svg>+32471902368</li>
        <li><svg viewBox="0 0 24 24"><rect x="2" y="5" width="20" height="14" rx="1"/><path d="M2 6l10 7 10-7"/></svg>info@rijwielwerkplaats-vanhoutte.be</li>
        <li><svg viewBox="0 0 24 24"><circle cx="12" cy="12" r="10"/><path d="M2 12h20M12 2a15 15 0 0 1 0 20M12 2a15 15 0 0 0 0 20"/></svg>www.rijwielwerkplaats-vanhoutte.be</li>
      </ul>
    </div>

    <p class="address">Kerkweg 46<br>9940 Bellebeke</p>
  </section>

</body>
</html>
```